Business Card Design Project

Business Card
We are rebranding with a new logo
Industry/Entity Type
Business
Contact Information for Business Card
Dennis Morvale +61 487215963 dennis@quorv.com.au P.O. Box 872 Fernlow QLD 4309
Requirements
Must have
- Logo

```html
<!DOCTYPE html>
<html lang="en">
<head>
<meta charset="utf-8">
<title>Quorv International — Business Card</title>
<link href="https://fonts.googleapis.com/css2?family=Questrial&display=swap" rel="stylesheet">
<style>
  :root {
    --backdrop: #5a5a5a;
    --card-top: #ffffff;
    --card-bottom: #e4e4e4;
    --brand-blue: #1c5f86;
    --brand-blue-light: #1f88b4;
    --brand-orange: #d36f22;
    --text-grey: #555a5e;
  }
  * { margin: 0; padding: 0; box-sizing: border-box; }
  html, body {
    width: 1200px; height: 965px; overflow: hidden;
    background: var(--backdrop);
    font-family: "Questrial", "Century Gothic", sans-serif;
  }
  .card {
    position: absolute; left: 40px; top: 162px;
    width: 1120px; height: 640px;
    border-radius: 40px; overflow: hidden;
    background: linear-gradient(170deg, var(--card-top) 0%, var(--card-top) 35%, var(--card-bottom) 100%);
  }
  .brand-name {
    position: absolute; left: 51px; top: 150px;
    font-size: 44px; color: var(--brand-blue);
    letter-spacing: 1px; line-height: 1;
  }
  .holder-name {
    position: absolute; left: 51px; top: 360px;
    font-size: 31px; color: var(--brand-blue);
    letter-spacing: 0.5px; line-height: 1;
    white-space: nowrap;
  }
  .name-rule { position: absolute; left: 0; top: 0; }
  .contact-list {
    position: absolute; left: 51px; top: 434px;
    list-style: none;
  }
  .contact-list li {
    display: flex; align-items: center;
    height: 33px; font-size: 26px; color: var(--text-grey);
    white-space: nowrap;
  }
  .contact-list svg { width: 26px; height: 26px; margin-right: 18px; flex: none; }
  .postal {
    position: absolute; left: 400px; top: 467px;
    font-size: 26px; line-height: 33px; color: var(--text-grey);
    white-space: nowrap;
  }
  .footer-band {
    position: absolute; left: 0; right: 0; bottom: 0; height: 100px;
    background: linear-gradient(180deg, rgba(211,111,34,0.85) 0%, var(--brand-blue) 100%);
  }
</style>
</head>
<body>
  <div class="card">
    <div class="brand-name">Quorv International</div>

    <div class="holder-name">DENNIS MORVALE</div>
    <svg class="name-rule" width="1120" height="640" aria-hidden="true">
      <circle cx="350" cy="376" r="4" fill="var(--brand-blue)"/>
      <line x1="350" y1="376" x2="738" y2="376" stroke="var(--brand-blue)" stroke-width="2"/>
      <line x1="738" y1="376" x2="1091" y2="376" stroke="var(--brand-orange)" stroke-width="2"/>
    </svg>

    <ul class="contact-list">
      <li>
        <svg viewBox="0 0 24 24" aria-hidden="true"><path fill="var(--brand-blue)" d="M6.6 2.5l3 3.4-1.8 2.6c1 2.4 3.3 4.7 5.7 5.7l2.6-1.8 3.4 3-1.7 3.4C11 19 5 13 3.2 4.2z"/></svg>
        +61 487215963
      </li>
      <li>
        <svg viewBox="0 0 24 24" aria-hidden="true"><rect x="2" y="5" width="20" height="14" fill="var(--brand-blue)"/><path d="M2.5 5.5l9.5 8 9.5-8M2.5 18.5l7-6.5M21.5 18.5l-7-6.5" stroke="#fff" stroke-width="1.4" fill="none"/></svg>
        dennis@quorv.com.au
      </li>
      <li>
        <svg viewBox="0 0 24 24" aria-hidden="true"><g fill="none" stroke="var(--brand-blue)" stroke-width="1.8"><circle cx="12" cy="12" r="9.5"/><ellipse cx="12" cy="12" rx="4" ry="9.5"/><path d="M2.5 12h19M4 7h16M4 17h16"/></g></svg>
        www.quorv.com.au
      </li>
    </ul>

    <div class="postal">P.O. Box 872 Fernlow<br>QLD 4309</div>

    <div class="footer-band" role="img" aria-label="Decorative orange and blue swoosh along the bottom edge of the card"></div>
  </div>
</body>
</html>
```